Business card design needed to incorporate existing logo

We need a business card for a new modern Accounting & Business Solutions company call TelmaNord Partners.com.au servicing all of Australia.
My tagline is Steady Ledger Answers... that deliver.

We specialise in Cloud Accounting and this is our primary focus. We also provide tax representation, debt recovery, computer, tablet and smart phone sales.

I would like a design that uses my corporate, trustworthy colours of blue/white, black/grey however am open to suggestion. I have attached my logo to go on the card somewhere,of which you will see the colour scheme.

I am after a card that STANDS OUT, somewhere between it not being too busy and not being a baron waste of space.

A 'cloud' incorporated in the design may work well, up to your artistic judgement. I know what I like when I see it; it is harder to put into words!

Excited to see your ideas!
I have added my logo predominately (blue/white) and for additional opportunity have added my reverse logo (darker one). I have used the blue/white on my website and letterhead. I will be using both on my vehicle signage.

Target Market(s)

Tradesmen and small-medium businesses of all descriptions Australia-wide

Industry/Entity Type

Debt

Contact Information for Business Card

Doug Hallett
Principal (optional)
TelmaNord Partners.com.au
Steady Ledger Answers... that deliver

P: 1800 493 518
M: 0412 658 071 (optional)
W: www.telmanordpartners.com.au
E: admin@telmanordpartners.com.au

Logo Text

Steady Ledger Answers... that deliver!

Logo styles of interest
Wordmark Logo
Requirements
Must have
• Must look professional and of high quality not cheap.

My logo and my tagline 'Steady Ledger Answers... that deliver'.

I have my colourscheme in mind as per my attached logo, however am open to suggestion. I want to see what you can create that I would not have thought of.

Modern, innovative.
Something I won't look at and think, 'I could have done that myself'.

Must be able to be printed on Prinvo 300gm premium cards and the artwork provided to me.
Nice to have
• Title of Principal is optional depending on space and judement call of look/fee.
M: (mobile) number is also optional as above.

Somthing cloud related given the Cloud Accounting aspect may be relevant. I leave it to your artistic design and judgement.
Should not have
• Must not look cheap.

```html
<!DOCTYPE html>
<html lang="en">
<head>
<meta charset="utf-8">
<title>TelmaNord Partners – Business Card</title>
<link href="https://fonts.googleapis.com/css2?family=Saira+Condensed:wght@500;600;700&family=Arimo:wght@700&display=swap" rel="stylesheet">
<style>
  :root{
    --navy:#1a2556;
    --sky:#3d8fd6;
    --paper-light:#f4f4f5;
    --paper-shade:#d9d9db;
    --ink:#1c1c1c;
    --name-ink:#1f2a5c;
    --backdrop:#8d8d8f;
    --white:#ffffff;
  }
  *{margin:0;padding:0;box-sizing:border-box}
  html,body{width:1200px;height:1200px;overflow:hidden}
  body{
    background:var(--backdrop);
    display:flex;flex-direction:column;align-items:center;justify-content:center;gap:56px;
  }
  .card{
    width:900px;height:514px;position:relative;overflow:hidden;
    box-shadow:0 10px 24px rgba(0,0,0,.28);
  }

  /* Back of card */
  .card-back{
    background:linear-gradient(160deg,var(--white) 0%,var(--paper-light) 45%,var(--paper-shade) 100%);
  }
  .card-back .brand-band{
    position:absolute;left:0;right:0;top:165px;height:150px;
    background:var(--navy);
    display:flex;align-items:center;justify-content:center;
    box-shadow:0 6px 8px rgba(0,0,0,.22);
  }
  .card-back .brand-wordmark{
    font-family:"Saira Condensed",sans-serif;font-weight:500;
    font-size:46px;letter-spacing:6px;text-transform:uppercase;color:var(--sky);
  }

  /* Front of card */
  .card-front{display:flex;background:var(--paper-light)}
  .brand-panel{
    width:405px;height:100%;background:var(--navy);
    display:flex;flex-direction:column;align-items:center;justify-content:center;
    padding:0 22px;
  }
  .brand-dot{
    width:150px;height:150px;border-radius:50%;background:var(--sky);margin-bottom:26px;
  }
  .brand-name{
    font-family:"Saira Condensed",sans-serif;font-weight:700;
    font-size:35px;line-height:1;text-transform:uppercase;color:var(--sky);
    letter-spacing:.3px;white-space:nowrap;
  }
  .brand-tagline{
    margin-top:6px;
    font-family:"Saira Condensed",sans-serif;font-weight:600;
    font-size:21px;text-transform:uppercase;color:var(--white);white-space:nowrap;
  }
  .details-panel{
    flex:1;position:relative;
    background:linear-gradient(150deg,var(--paper-shade) 0%,var(--paper-light) 40%,var(--white) 100%);
  }
  .person{position:absolute;top:70px;right:40px;text-align:left}
  .person-name{
    font-family:"Saira Condensed",sans-serif;font-weight:700;
    font-size:44px;line-height:1;text-transform:uppercase;color:var(--name-ink);
  }
  .person-title{
    font-family:"Saira Condensed",sans-serif;font-weight:600;
    font-size:18px;text-transform:uppercase;color:var(--ink);
  }
  .contact-list{
    position:absolute;left:42px;bottom:62px;list-style:none;
    font-family:"Arimo",sans-serif;font-weight:700;font-size:19px;line-height:1.35;color:var(--ink);
    letter-spacing:.6px;
  }
</style>
</head>
<body>
  <section class="card card-back" aria-label="Card back">
    <div class="brand-band">
      <span class="brand-wordmark">TelmaNord Partners.com.au</span>
    </div>
  </section>

  <section class="card card-front" aria-label="Card front">
    <div class="brand-panel">
      <div class="brand-dot"></div>
      <div class="brand-name">TelmaNordPartners.com.au</div>
      <div class="brand-tagline">Steady Ledger Answers... that deliver</div>
    </div>
    <div class="details-panel">
      <div class="person">
        <div class="person-name">Doug Hallett</div>
        <div class="person-title">Principal</div>
      </div>
      <ul class="contact-list">
        <li>P : 1800 493 518</li>
        <li>M: 0412 658 071</li>
        <li>E : admin@telmanordpartners.com.au</li>
      </ul>
    </div>
  </section>
</body>
</html>
```